Kestrel Facilities Business Card Design

We would now like to design business cards with the new Kestrel Facilities logo

Target Market(s)

Professional

Industry/Entity Type

Professional services

Contact Information for Business Card

Employee name, title, phone number, email address, corporate office address and logo.

Font styles to use
Sans Serif

Colors
0054AA
0677BA
7BADD7
CADEEF
E8F1F8

Requirements
Must have
• My logo
Should not have
• any other pictures or images besides my logo

```html
<!DOCTYPE html>
<html lang="en">
<head>
<meta charset="utf-8">
<title>Kestrel Facilities Business Card</title>
<link href="https://fonts.googleapis.com/css2?family=Montserrat:wght@400;500;700&display=swap" rel="stylesheet">
<style>
  :root {
    --card-blue: #3676BD;
    --card-white: #FFFFFF;
    --swoosh-grey: #A3A3A3;
    --silver: #CAD3E2;
    --backdrop: #2B2B2E;
  }
  * { box-sizing: border-box; margin: 0; padding: 0; }
  html, body {
    width: 1200px; height: 900px; overflow: hidden;
    background: var(--backdrop);
    font-family: "Montserrat", sans-serif;
  }
  .sheet {
    width: 1200px; height: 900px;
    display: flex; flex-direction: column;
    align-items: center; justify-content: center; gap: 40px;
  }
  .card {
    position: relative;
    width: 665px; height: 380px;
    border-radius: 26px;
    overflow: hidden;
  }
  .card--front { background: var(--card-white); }
  .card--back { background: var(--card-blue); display: flex; align-items: center; justify-content: center; }
  .front-shape { position: absolute; inset: 0; width: 100%; height: 100%; }
  .contact {
    position: absolute; left: 40px; top: 150px;
    color: var(--card-white);
  }
  .contact__name { font-weight: 700; font-size: 25px; letter-spacing: 0.5px; text-transform: uppercase; }
  .contact__title { font-size: 17px; margin-top: 2px; margin-bottom: 14px; }
  .contact__line { font-size: 15.5px; line-height: 1.45; display: flex; align-items: center; gap: 8px; }
  .contact__line svg { width: 15px; height: 15px; flex: none; }
  .contact__address { margin-bottom: 6px; }
  .brand {
    position: absolute; right: 46px; top: 150px;
    display: flex; align-items: center; gap: 12px;
    color: var(--card-blue);
  }
  .brand__mark { width: 30px; height: 30px; background: currentColor; }
  .brand__name { font-weight: 700; font-size: 27px; letter-spacing: 0.5px; }
  .brand--back { position: static; color: var(--silver); }
  .brand--back .brand__mark { width: 44px; height: 44px; }
  .brand--back .brand__name { font-size: 40px; }
</style>
</head>
<body>
<main class="sheet">
  <section class="card card--front">
    <svg class="front-shape" viewBox="0 0 665 380" preserveAspectRatio="none" aria-hidden="true">
      <path d="M0,55 C160,62 300,120 345,215 C385,305 440,365 540,380 L0,380 Z" fill="var(--card-blue)"/>
      <path d="M150,58 C270,80 330,130 360,210 C395,300 450,355 555,372" fill="none" stroke="var(--swoosh-grey)" stroke-width="8"/>
    </svg>
    <div class="contact">
      <p class="contact__name">Dana Whitcombe</p>
      <p class="contact__title">Co-Founder</p>
      <p class="contact__line">4180 N. Harbor Lane</p>
      <p class="contact__line contact__address">Suite 702 Easton.14</p>
      <p class="contact__line">
        <svg viewBox="0 0 16 16" aria-hidden="true"><path fill="#fff" d="M3 2h3l1 3-2 1c1 2 3 4 5 5l1-2 3 1v3c0 1-1 1-1 1C7 14 2 9 2 3c0 0 0-1 1-1z"/></svg>
        +254-700-41226
      </p>
      <p class="contact__line">
        <svg viewBox="0 0 16 16" aria-hidden="true"><rect x="1" y="3" width="14" height="10" fill="none" stroke="#fff" stroke-width="1.6"/><path d="M1 3l7 6 7-6" fill="none" stroke="#fff" stroke-width="1.6"/></svg>
        info@kestrelfacilities.com
      </p>
    </div>
    <div class="brand">
      <span class="brand__mark"></span>
      <span class="brand__name">Kestrel Facilities</span>
    </div>
  </section>

  <section class="card card--back">
    <div class="brand brand--back">
      <span class="brand__mark"></span>
      <span class="brand__name">Kestrel Facilities</span>
    </div>
  </section>
</main>
</body>
</html>
```